Construction Company

Design a clutter free business card, it can be double-sided utilizing the logo for VKM Ltd simple with all relevant contact information.

Please also a letterhead design to function for the purposes of invoicing, all mail requirements, with header to be distinctive while the footer ties page together and incorporates all necessary information.

For now, please use generic / dummy text and when a winner is selected, I will disclose the contact information.

Hi Designers! Please read the updated brief which includes the design of a business card and letterhead. Thank you!

```html
<!DOCTYPE html>
<html lang="en">
<head>
<meta charset="utf-8">
<title>VKM Ltd – Letterhead and Envelope</title>
<link href="https://fonts.googleapis.com/css2?family=Open+Sans:wght@400;600&family=Lato:wght@400&display=swap" rel="stylesheet">
<style>
  :root {
    --navy: #1b2f8c;
    --gold: #b38f0c;
    --gold-soft: #d9c37a;
    --ink: #4a4a4a;
    --paper: #ffffff;
    --backdrop: #e4e4e4;
  }
  * { box-sizing: border-box; margin: 0; padding: 0; }
  html, body { width: 1200px; height: 1200px; overflow: hidden; }
  body {
    background: var(--backdrop);
    position: relative;
    font-family: "Open Sans", sans-serif;
    color: var(--ink);
  }
  .sheet {
    position: absolute;
    background: var(--paper);
    box-shadow: 0 2px 8px rgba(0,0,0,0.18);
    overflow: hidden;
  }
  .brand {
    position: absolute;
    display: flex;
    align-items: center;
    gap: 6px;
    font-family: "Open Sans", sans-serif;
    font-weight: 600;
    color: var(--navy);
    white-space: nowrap;
  }
  .brand-dot {
    display: inline-block;
    border-radius: 50%;
    background: var(--gold);
  }
  .corner-motif {
    position: absolute;
    background: linear-gradient(90deg, var(--gold), var(--gold-soft));
    border-radius: 0 50% 50% 0;
  }

  /* Letterhead */
  .letterhead { left: 119px; top: 278px; width: 556px; height: 714px; }
  .letterhead .brand { left: 50%; top: 24px; transform: translateX(-50%); font-size: 30px; }
  .letterhead .brand-dot { width: 11px; height: 11px; }
  .letter-body {
    position: absolute;
    left: 52px; top: 130px;
    width: 450px;
    font-size: 8.8px;
    line-height: 11px;
  }
  .letter-body .date { margin-bottom: 10px; }
  .letter-body .recipient { margin-bottom: 29px; }
  .letter-body .salutation { margin-bottom: 19px; }
  .letter-body .para {
    line-height: 16px;
    text-align: justify;
    hyphens: auto;
    margin-bottom: 16px;
  }
  .letter-body .closing { margin-top: 28px; }
  .signatory { margin-top: 37px; }
  .signatory .name { font-size: 11.5px; color: #333; line-height: 14px; }
  .signatory .role { font-size: 8.8px; margin-top: 5px; }

  .letterhead .corner-motif { left: 0; top: 582px; width: 61px; height: 132px; }
  .letter-footer {
    position: absolute;
    left: 53px; right: 0;
    top: 631px; height: 52px;
    background: var(--gold);
    color: #fff;
    font-family: "Lato", sans-serif;
    font-size: 11px;
    text-align: center;
    padding-top: 7px;
    line-height: 18px;
    padding-right: 30px;
  }

  /* Envelope front */
  .envelope-front { left: 715px; top: 492px; width: 432px; height: 215px; }
  .envelope-front .brand { left: 26px; top: 24px; font-size: 20px; }
  .envelope-front .brand-dot { width: 7px; height: 7px; }
  .envelope-front .corner-motif { left: 0; top: 132px; width: 37px; height: 83px; }
  .return-band {
    position: absolute;
    left: 37px; right: 0;
    top: 162px; height: 31px;
    background: var(--gold);
    color: #fff;
    font-family: "Lato", sans-serif;
    font-size: 8.5px;
    line-height: 31px;
    padding-left: 10px;
  }

  /* Envelope back */
  .envelope-back { left: 717px; top: 743px; width: 429px; height: 212px; }
  .envelope-flap { position: absolute; left: 0; top: 0; }
</style>
</head>
<body>

<section class="sheet letterhead">
  <div class="brand"><span class="brand-dot"></span>VKM Ltd</div>

  <div class="letter-body">
    <p class="date">Issuing Date: May 5, 2018</p>
    <p class="recipient">Name Of Employee Mr. XYZABC<br>Address of Employee<br>Address Line 2 etc..</p>
    <p class="salutation">Dear Mr.XYZABC</p>
    <p class="para">Lorem Ipsum has been the industry's standard dummy text ever since the 1500s, when an unknown printer took a galley of type and scrambled it to make a type specimen book. It has survived not only five centuries, but also the leap into electronic typesetting, remaining essentially unchanged. It was popularised in the 1960s with the release of Lindwell sheets containing Lorem Ipsum passages, and more recently with desktop publishing software like Ferrow PageSetter including versions of Lorem Ipsum.</p>
    <p class="para">Lorem Ipsum is simply dummy text of the printing and typesetting industry. Lorem Ipsum has been the industry's standard dummy text ever since the 1500s, when an unknown printer took a galley of type and scrambled it to make a type specimen book.</p>
    <p class="para">It has survived not only five centuries, but also the leap into electronic typesetting, remaining essentially unchanged. It was popularised in the 1960s with the release of Lindwell sheets containing Lorem Ipsum passages.</p>
    <p class="closing">Yours Sincerely</p>
    <div class="signatory">
      <p class="name">Daniel Hartwell</p>
      <p class="role">Managing Director</p>
    </div>
  </div>

  <div class="corner-motif" role="img" aria-label="Gold flower ornament at the footer corner"></div>
  <footer class="letter-footer">
    421, Address line here,&nbsp; dummy code 45452 Country Name<br>
    P: 044-555 210 300 | M: 044-555 210 300 | E: info@vkmbuild.com | www.vkmbuild.com
  </footer>
</section>

<section class="sheet envelope-front">
  <div class="brand"><span class="brand-dot"></span>VKM Ltd</div>
  <div class="corner-motif" role="img" aria-label="Gold flower ornament at the band corner"></div>
  <div class="return-band">421, Address line goes here Country Name, 45452</div>
</section>

<section class="sheet envelope-back">
  <svg class="envelope-flap" width="429" height="52" viewBox="0 0 429 52" role="img" aria-label="Envelope flap with repeating gold flower pattern">
    <polygon points="0,0 429,0 411,50 18,50" fill="var(--gold)"/>
  </svg>
</section>

</body>
</html>
```